CONTACT US Page and design for website

We need a contact us page for our website. We would like it to have a message area, a map, our information, etc.

Please see the text attachment for what we are looking for. We need to have something that is creative and interesting, modern and professional.

We believe that a contact US page should be very creative because everyone clicks that to contact us. We want it to be super professional, attention grabbing, pleasing to the eye.

PLEASE KEEP THE HEADER AND FOOTER THE SAME, ONLY THE ACTUAL CONTACT US PAGE NEEDS TO BE WORKED ON. THANKS!
We are excited to work with designers for this project.

Target Market(s)

Clients in technology business

Industry/Entity Type

Information Technology

Number of Pages Required

1 page

Font styles to use
Serif

Requirements
Must have
• CHECK THE TEXT ATTACHMENT PLEASE
• Must stay within our design colors and theme.
Nice to have
• see attachment
Should not have
• it should be special

```html
<!DOCTYPE html>
<html lang="en">
<head>
<meta charset="utf-8">
<title>Contact Us – Nexora Tech</title>
<link href="https://fonts.googleapis.com/css2?family=Open+Sans:ital,wght@0,400;0,600;0,700;1,600&family=Poiret+One&family=Arimo:wght@400&display=swap" rel="stylesheet">
<style>
:root{
  --teal:#2cc4b3;
  --teal-dark:#16877f;
  --teal-text:#1f9a8e;
  --ink:#333;
  --muted:#888;
  --line:#d9d9d9;
  --panel:#f2f2f2;
  --foot:#a6a6a6;
  --foot-dark:#9a9a9a;
  --tab:#7d7d7d;
}
*{box-sizing:border-box;margin:0;padding:0}
html,body{width:855px;height:1200px;overflow:hidden;background:#fff}
body{position:relative;font-family:"Open Sans",sans-serif;color:var(--ink)}
.abs{position:absolute}

/* header */
.brand{left:45px;top:17px;display:flex;align-items:center;gap:12px}
.brand-mark{width:34px;height:34px;border-radius:50%;background:var(--teal)}
.brand-name{font-size:25px;font-weight:400;letter-spacing:3px;color:var(--teal)}
.account-tab{left:676px;top:0;width:136px;height:23px;border-radius:0 0 18px 18px;background:#9b9b9b;overflow:hidden;display:flex;font-size:7.5px;color:#333}
.account-tab span{flex:1;display:flex;align-items:center;justify-content:center}
.account-tab span+span{background:var(--tab);color:#eee}
.circle-btn{width:29px;height:29px;border-radius:50%;border:1px solid var(--line);display:flex;align-items:center;justify-content:center}
.chat{left:598px;top:33px}
.chat-label{left:635px;top:43px;font-size:9.5px;color:#555}
.call{left:695px;top:33px}
.call-num{left:734px;top:39px;font-family:Arimo,sans-serif;font-size:13.5px;color:#444}
.rule{left:0;width:855px;height:1px;background:var(--line)}
.nav{left:44px;top:81px;display:flex;gap:18.5px;font-size:7.8px;color:#333;letter-spacing:.3px}
.search{left:664px;top:78px;width:118px;height:24px;border:1px solid #ccc;border-radius:12px;font-size:7.5px;padding:7px 14px;color:#444}
.search svg{position:absolute;right:8px;top:6px}
.cart{left:788px;top:76px}

/* map */
.map{left:38px;top:107px;width:780px;height:283px;background:linear-gradient(135deg,#ececec,#e2e4e3 60%,#e8ebe8)}
.section{left:38px;top:390px;width:780px;height:354px;background:var(--panel)}

.hq{left:496px;top:314px;width:294px;height:134px;background:var(--teal);color:#fff;padding:14px 16px}
.hq h1{font-size:23px;font-weight:700;color:#111;margin-bottom:10px}
.hq h2{font-size:14.5px;font-weight:700;margin-bottom:2px}
.hq p{font-size:14px;line-height:20px}

.msg-title{left:66px;top:420px;font-family:"Poiret One",sans-serif;font-size:21px;color:#333}
.field{background:#f2f2f2;border:1px solid var(--line);font-size:8px;color:#888;padding:13px 11px}
.submit{left:367px;top:685px;width:111px;height:33px;background:#333;color:#eee;font-size:11.5px;letter-spacing:2px;display:flex;align-items:center;justify-content:center}

.side-h{font-size:12px;font-weight:700;color:var(--teal);letter-spacing:1px}
.hours{left:514px;top:502px;font-size:9px;color:#333;line-height:18.8px}
.hours .d{display:inline-block;width:68px}
.note{left:514px;top:612px;width:272px;font-size:9.3px;font-style:italic;font-weight:600;line-height:15px;color:#222}
.social{left:516px;top:690px;display:flex;gap:18px}
.social span{width:28px;height:28px;border-radius:50%;background:#222;display:block}

/* inquiry cards */
.card{top:769px;width:236px;height:104px;border:1px solid #ccc;border-bottom:none;padding:17px 20px}
.card::after{content:"";position:absolute;left:-1px;right:-1px;bottom:0;height:3px;background:linear-gradient(90deg,var(--teal-dark) 68%,var(--teal) 68%)}
.card h3{font-size:11.8px;font-weight:600;color:var(--teal-text);margin-bottom:4px}
.card p{font-size:14px;line-height:20px;color:#333}

/* footer */
.foot{left:0;top:898px;width:855px;height:196px;background:var(--foot);color:#fff;font-family:Arimo,sans-serif}
.foot-copy{left:54px;top:12px;width:747px;text-align:center;font-size:10.8px;line-height:14px}
.foot-rule{left:130px;top:64px;width:530px;height:1px;background:#bdbdbd}
.foot-info{top:80px;font-size:10.6px;line-height:14px;display:flex;gap:8px}
.foot-links{top:133px;font-size:12px}
.support{left:660px;top:133px;width:140px;text-align:center;font-size:12px}
.support small{display:block;font-size:7px;font-weight:700;line-height:10px}
.foot2{left:0;top:1094px;width:855px;height:106px;background:var(--foot-dark);color:#fff;font-family:Arimo,sans-serif}
.ring{top:15px;width:27px;height:27px;border-radius:50%;border:1px solid #ddd}
.foot2-rule{left:130px;top:56px;width:590px;height:1px;background:#b5b5b5}
.legal{left:380px;top:67px;font-size:9.5px;line-height:13px;display:flex;gap:8px;align-items:center}
.legal i{width:16px;height:16px;background:#ddd;display:block}
</style>
</head>
<body>

<header>
  <div class="abs brand"><span class="brand-mark"></span><span class="brand-name">NEXORA</span></div>
  <div class="abs account-tab"><span>SIGN UP</span><span>LOGIN</span></div>
  <div class="abs circle-btn chat"><svg width="14" height="12" viewBox="0 0 14 12"><path d="M1 1h12v7H6l-3 3V8H1z" fill="var(--teal)"/></svg></div>
  <div class="abs chat-label">LIVE CHAT</div>
  <div class="abs circle-btn call"><svg width="12" height="12" viewBox="0 0 12 12"><path d="M2 1l2 0 1 3-1.5 1a6 6 0 0 0 3.5 3.5L8 7l3 1v2c0 1-1 1-1 1C5 11 1 7 1 2c0 0 0-1 1-1z" fill="var(--teal)"/></svg></div>
  <div class="abs call-num">555-014-2290</div>
  <div class="abs rule" style="top:71px"></div>
  <nav class="abs nav"><span>SERVERS</span><span>WORKSTATIONS</span><span>COMPONENTS</span><span>VIRTUAL REALITY</span><span>DRONES</span><span>ABOUT US</span><span>BLOG</span><span>RESOURCES</span><span>CONTACT US</span></nav>
  <div class="abs search">Search<svg width="12" height="12" viewBox="0 0 12 12"><circle cx="5" cy="5" r="3.6" fill="none" stroke="var(--teal)" stroke-width="1.6"/><path d="M7.6 7.6L11 11" stroke="var(--teal)" stroke-width="1.6"/></svg></div>
  <div class="abs circle-btn cart"><svg width="14" height="12" viewBox="0 0 14 12"><path d="M1 3h12l-1.5 8h-9z" fill="none" stroke="var(--teal)" stroke-width="1.4"/><path d="M4 3l2-2M10 3L8 1" stroke="var(--teal)" stroke-width="1.2"/></svg></div>
  <div class="abs rule" style="top:106px"></div>
</header>

<main>
  <div class="abs map" role="img" aria-label="Street map showing the office location in Fernvale"></div>
  <div class="abs section"></div>

  <section class="abs hq">
    <h1>Contact Us</h1>
    <h2>OFFICE HEADQUARTERS</h2>
    <p>Nexora Tech, LLC.<br>4820 Larkspur Ave. Fernvale, CA 91000</p>
  </section>

  <h2 class="abs msg-title">Message center to contact us. Must have:</h2>
  <div class="abs field" style="left:62px;top:472px;width:200px;height:38px">FIRST NAME</div>
  <div class="abs field" style="left:278px;top:472px;width:200px;height:38px">LAST NAME</div>
  <div class="abs field" style="left:62px;top:524px;width:200px;height:38px;padding-left:16px">EMAIL</div>
  <div class="abs field" style="left:278px;top:524px;width:200px;height:38px">PHONE</div>
  <div class="abs field" style="left:62px;top:576px;width:416px;height:98px">MASSAGE</div>
  <div class="abs submit">SUBMIT</div>

  <h3 class="abs side-h" style="left:514px;top:471px">HOURS OF OPERATION</h3>
  <div class="abs hours">
    <div><span class="d">Monday</span>: 8:00am- 5:00pm</div>
    <div><span class="d">Tuesday</span>: 8:00am- 5:00pm</div>
    <div><span class="d">Wednesday</span>: 8:00am- 5:00pm</div>
    <div><span class="d">Thursday</span>: 8:00am- 5:00pm</div>
    <div><span class="d">Friday</span>: 8:00am- 5:00pm</div>
  </div>
  <p class="abs note">Our dedicated customer service representatives are available 24/7 by phone.</p>
  <h3 class="abs side-h" style="left:514px;top:662px">STAY CONNECTED:</h3>
  <div class="abs social" aria-label="Social links"><span></span><span></span><span></span><span></span></div>

  <div class="abs card" style="left:38px"><h3>General Inquiries</h3><p>(555)014-2290<br>info@nexoratech.com</p></div>
  <div class="abs card" style="left:310px"><h3>Sales Inquiries</h3><p>(555)014-2290<br>sales@nexoratech.com</p></div>
  <div class="abs card" style="left:581px"><h3>Purchasing Inquiries</h3><p>(555)014-2291<br>purchasing@nexoratech.com</p></div>
</main>

<footer>
  <div class="abs foot">
    <p class="abs foot-copy">Based in Fernvale California, Nexora Tech offers custom servers, storage, and workstations for local businesses in Los Angeles, Beverly Hills, Thousand Oaks, Ventura, Orange County, Santa Barbara, Oxnard, Irvine, Anaheim, and San Diego. Nexora Tech also offers such products to clients throughout the United States and Worldwide.</p>
    <div class="abs foot-rule"></div>
    <div class="abs foot-info" style="left:100px"><svg width="8" height="11" viewBox="0 0 8 11"><path d="M4 0a4 4 0 0 1 4 4c0 3-4 7-4 7S0 7 0 4a4 4 0 0 1 4-4z" fill="#fff"/><circle cx="4" cy="4" r="1.4" fill="var(--foot)"/></svg><span>4820 Larkspur Ave.<br>Fernvale, CA 91000</span></div>
    <div class="abs foot-info" style="left:359px"><svg width="10" height="10" viewBox="0 0 12 12"><path d="M2 1l2 0 1 3-1.5 1a6 6 0 0 0 3.5 3.5L8 7l3 1v2c0 1-1 1-1 1C5 11 1 7 1 2c0 0 0-1 1-1z" fill="#fff"/></svg><span>555-014-2290</span></div>
    <div class="abs foot-info" style="left:588px"><svg width="10" height="8" viewBox="0 0 10 8"><rect width="10" height="8" fill="#fff"/><path d="M0 0l5 4 5-4" fill="none" stroke="var(--foot)"/></svg><span>sales@nexoratech.com</span></div>
    <div class="abs foot-links" style="left:73px">Computer Hardware</div>
    <div class="abs foot-links" style="left:271px">Drones</div>
    <div class="abs foot-links" style="left:378px">Virtual Reality</div>
    <div class="abs foot-links" style="left:531px">About Us</div>
    <div class="abs support">Customer Support<small style="margin-top:2px">Terms and Conditions</small><small>Warranty Information</small><small>Contact Us</small><small>Return Policy</small></div>
  </div>
  <div class="abs foot2">
    <span class="abs ring" style="left:351px"></span>
    <span class="abs ring" style="left:389px"></span>
    <span class="abs ring" style="left:427px"></span>
    <span class="abs ring" style="left:465px"></span>
    <div class="abs foot2-rule"></div>
    <div class="abs legal"><i></i><span>Nexora Tech, LLC.<br>Copyright © 2017</span></div>
  </div>
</footer>

</body>
</html>
```